Fizz's Shed & Grill Burger Restaurant Website - HomePage Only PSD

I need a website design for a restaurant called "Fizz's Shed and Grill" featuring burgers, wings, beer, live music, trivia, and more. I have several images of the restaurant and they already have their logo files created (see attached). I want some type of wood background and integrate the silver tin. This needs to be a modern, hip and fun type design. Design must incorporate these attached graphics.

UPDATE - just added a few more images of things I really like to be incorporated into my designs.
Updates

Industry/Entity Type

Burger Restaurant

Number of Pages Required

1 page

Font styles to use
Sans Serif

Requirements
Must have
• Restaurant/Bar theme with integration of existing logo and the red wood look.
Nice to have
• - Modern Fun appearance
• - Use Pelko Fonts

```html
<!DOCTYPE html>
<html lang="en">
<head>
<meta charset="utf-8">
<title>Fizz's Shed and Grill</title>
<link href="https://fonts.googleapis.com/css2?family=Kalam:wght@400;700&family=Open+Sans:wght@400;600;700&display=swap" rel="stylesheet">
<style>
:root{
  --wood-dark:#2a1208;
  --wood:#4a2210;
  --wood-mid:#5c2c15;
  --wood-line:rgba(20,6,2,.35);
  --wood-light:rgba(140,70,35,.18);
  --text-light:#e9d9c8;
  --text-muted:#cbb8a4;
  --silver-1:#f7f7f7;
  --silver-2:#c9c9c9;
  --silver-3:#9a9a9a;
  --ink:#2b2b2b;
  --grey-text:#555;
  --paper:#f2f2f2;
}
*{box-sizing:border-box;margin:0;padding:0}
html,body{width:1200px;height:2731px;overflow:hidden}
body{
  position:relative;
  font-family:"Open Sans",Arial,sans-serif;
  color:var(--text-light);
  background:
    linear-gradient(90deg,rgba(15,5,2,.55) 0%,transparent 14%,transparent 86%,rgba(15,5,2,.55) 100%),
    repeating-linear-gradient(90deg,transparent 0 37px,var(--wood-line) 37px 39px,transparent 39px 83px,var(--wood-line) 83px 84px,transparent 84px 131px,var(--wood-light) 131px 140px,transparent 140px 171px),
    repeating-linear-gradient(90deg,transparent 0 9px,rgba(0,0,0,.07) 9px 10px,transparent 10px 23px,rgba(255,200,150,.04) 23px 25px,transparent 25px 31px),
    linear-gradient(180deg,var(--wood) 0%,var(--wood-mid) 50%,var(--wood) 100%);
}
.abs{position:absolute}
.script{font-family:"Kalam",cursive;font-weight:400}

/* hero */
.hero{left:0;top:0;width:1200px;height:565px;
  clip-path:polygon(0 0,1200px 0,1200px 483px,600px 565px,0 483px);
  background:linear-gradient(180deg,#3d4a3a 0%,#6f8a4a 22%,#9bb551 45%,#a9bd55 62%,#8a9e45 80%,#6d7d38 100%)}
.nav-line{left:182px;width:856px;height:2px;background:rgba(255,255,255,.55)}
.nav a{position:absolute;top:70px;color:#fff;font-family:"Kalam",cursive;font-size:20px;text-decoration:none;transform:translateX(-50%)}
.nav .home{top:56px;width:62px;height:62px;border:2px solid #fff;border-radius:50%;display:flex;align-items:center;justify-content:center}
.brand{left:545px;top:30px;width:110px;height:110px;border-radius:50%;background:var(--wood-dark);border:3px solid #fff;display:flex;align-items:center;justify-content:center;text-align:center;color:#fff;font-family:"Kalam",cursive;font-size:17px;line-height:1.1}
.hero-title{left:0;width:1200px;top:250px;text-align:center;font-size:54px;color:#fff;text-shadow:0 2px 6px rgba(0,0,0,.4)}
.hero-sub{left:330px;width:540px;top:320px;text-align:center;font-size:16px;font-style:italic;font-weight:600;color:#fff;line-height:1.45;text-shadow:0 1px 3px rgba(0,0,0,.35)}
.btn-start{left:520px;top:388px;width:160px;height:40px;background:#f1f1f1;color:#222;font-size:12px;font-weight:700;display:flex;align-items:center;justify-content:center;gap:5px;border-radius:2px}
.dots{left:562px;top:556px;display:flex;gap:7px}
.dots span{width:10px;height:10px;border-radius:50%;background:rgba(255,255,255,.45)}
.dots span:first-child{background:#fff}

/* welcome */
.h-section{font-size:38px;color:#fff;text-align:center}
.welcome-title{left:0;width:1200px;top:636px}
.welcome-text{left:280px;width:640px;top:702px;text-align:center;font-size:10.5px;line-height:19px;color:var(--text-muted)}
.card{top:843px;width:204px;height:237px;background:linear-gradient(120deg,var(--silver-2),var(--silver-1) 35%,var(--silver-3) 60%,var(--silver-1) 85%,var(--silver-2));text-align:center;color:var(--ink);padding-top:88px}
.card h3{font-size:22px;color:#222}
.card p{font-size:10.5px;line-height:17px;color:var(--grey-text);margin:6px 18px 0}
.card .more{display:inline-block;margin-top:10px;border:1px solid #333;padding:5px 8px;font-size:10px;font-weight:600;color:#222;background:rgba(255,255,255,.5)}
.card-photo{top:774px;width:146px;height:146px;border-radius:50%;border:4px solid #ddd}

/* our restaurant */
.rest-title{left:162px;top:1148px;font-size:36px;color:#fff}
.rest-text{left:162px;width:430px;top:1210px;font-size:10.5px;line-height:19px;color:var(--text-muted)}
.quick{top:1352px;width:66px;text-align:center}
.quick .ring{width:66px;height:66px;border:2px solid #fff;border-radius:50%;display:flex;align-items:center;justify-content:center}
.quick span{display:block;margin-top:14px;font-size:11px;color:#fff;white-space:nowrap}
.sign-photo{left:606px;top:1155px;width:446px;height:446px;border-radius:50%;border:14px solid #d9d9d9;box-shadow:0 0 0 6px #4a1f10,0 8px 20px rgba(0,0,0,.5);background:linear-gradient(160deg,#5a2a18 0%,#a44a2a 35%,#b8552f 65%,#8a3a20 100%);z-index:3}

/* news */
.news-band{left:0;top:1502px;width:1200px;height:404px;background:linear-gradient(180deg,#fdfdfd,var(--paper) 60%,#e3e3e3)}
.table-setting{left:0;top:1502px;width:360px;height:404px;background:linear-gradient(90deg,#e4e4e4 0%,#f7f7f7 55%,rgba(242,242,242,0) 100%)}
.burger{left:1030px;top:1612px;width:170px;height:282px;background:linear-gradient(160deg,#d9963c 0%,#c7812f 45%,#8a5a2a 100%)}
.news-title{left:410px;top:1638px;font-size:36px;color:#222}
.news-text{left:410px;width:560px;top:1706px;font-size:10.5px;line-height:19px;color:var(--grey-text)}
.news-meta{left:410px;top:1830px;font-size:10.5px;color:#333;font-weight:600}

/* events */
.events-title{left:0;width:1200px;top:1928px}
.event{top:1998px;width:277px}
.event-photo{height:191px;border:3px solid #e6e6e6}
.event h4{margin-top:14px;font-family:"Kalam",cursive;font-weight:400;font-size:21px;color:#fff;white-space:nowrap}
.event p{margin-top:6px;font-size:10.5px;line-height:17px;color:var(--text-muted)}
.event .more{display:inline-block;margin-top:14px;width:106px;height:38px;line-height:38px;text-align:center;font-size:10.5px;font-weight:700;color:#222;background:linear-gradient(90deg,var(--silver-2),var(--silver-1),var(--silver-3))}

/* footer */
.footer{left:0;top:2413px;width:1200px;height:318px;
  background:
    repeating-linear-gradient(90deg,transparent 0 41px,rgba(0,0,0,.3) 41px 43px,transparent 43px 97px,rgba(120,60,30,.12) 97px 105px,transparent 105px 149px),
    linear-gradient(90deg,#1a0a04,#2e150a 50%,#1a0a04)}
.footer-rule{left:0;width:1200px;height:0;border-top:2px dashed #8c6a55}
.footer-badge{left:582px;top:2391px;width:36px;height:36px;border-radius:50%;background:#2e150a;border:2px solid #fff}
.footer-brand{left:164px;top:2504px;width:133px;height:133px;border-radius:50%;border:3px solid #fff;display:flex;align-items:center;justify-content:center;text-align:center;color:#fff;font-family:"Kalam",cursive;font-size:18px;line-height:1.1}
.f-col{top:2460px}
.f-col h5{font-family:"Kalam",cursive;font-weight:400;font-size:22px;color:#fff;margin-bottom:12px}
.f-col p{font-size:10.5px;line-height:18px;color:var(--text-light)}
.hours div{display:flex;font-size:10.5px;line-height:19px;color:var(--text-light);width:200px}
.hours div i{flex:1;border-bottom:1px dotted #9c836f;margin:0 2px 6px}
.hours .sub{margin-top:2px;display:block}
.contact li{list-style:none;font-size:10.5px;line-height:19px;color:var(--text-light);display:flex;gap:8px}
.contact li svg{flex:none;margin-top:4px}
.social{display:flex;gap:6px;margin-top:12px}
.social span{width:24px;height:24px;border-radius:50%;border:1.5px solid #fff}
.copyright{left:0;width:1200px;top:2700px;text-align:center;font-size:10.5px;color:var(--text-light)}
</style>
</head>
<body>

<section class="abs hero" role="img" aria-label="Painted mural of green farm hills with a red barn, silos and grazing cows"></section>

<nav class="nav">
  <div class="abs nav-line" style="top:58px"></div>
  <div class="abs nav-line" style="top:115px"></div>
  <a class="home" style="left:215px">Home</a>
  <a style="left:328px">About</a>
  <a style="left:441px">Menu</a>
  <a style="left:734px">Events</a>
  <a style="left:860px">Gallery</a>
  <a style="left:974px">Contact</a>
  <div class="abs brand">Fizz's Shed<br>and Grill</div>
</nav>

<h1 class="abs hero-title script">Fizz's Shed and Grill</h1>
<p class="abs hero-sub">Sed ut perspiciatis unde omnis iste natus error sit voluptatem accusanti um dolore mq ue laudantium, totam rem aperiam, eaque ip.</p>
<div class="abs btn-start">GET STARTED HERE
  <svg width="11" height="11" viewBox="0 0 12 12"><circle cx="6" cy="6" r="5" fill="none" stroke="#222" stroke-width="1.3"/><path d="M5 3.5 7.5 6 5 8.5" fill="none" stroke="#222" stroke-width="1.3"/></svg>
</div>
<div class="abs dots"><span></span><span></span><span></span><span></span><span></span></div>

<h2 class="abs h-section script welcome-title">Welcome to Fizz's Shed and Grill</h2>
<p class="abs welcome-text">Sed ut perspiciatis unde omnis iste natus error sit voluptatem accusantium doloremque laudant ium, totam rem aperiam, eaque isa quae billo inventore veritatis et quasi architecto beatae vitae dicta sunt explicaboemo enim ipsamvoluptatem quia voluptas sit asperntur aut odit auSed ut pe rspiciatis unde omnis iste natus error sit voluptatem accusantium</p>

<article class="abs card" style="left:162px"><h3 class="script">Burgers</h3><p>Sed ut perspiciatis unde isna tus error sit voluptatem accntm dioremque laudant ium totre</p><span class="more">READ MORE</span></article>
<article class="abs card" style="left:386px"><h3 class="script">Wings</h3><p>Sed ut perspiciatis unde isna tus error sit voluptatem accntm dioremque laudant ium totre</p><span class="more">READ MORE</span></article>
<article class="abs card" style="left:608px"><h3 class="script">Beer</h3><p>Sed ut perspiciatis unde isna tus error sit voluptatem accntm dioremque laudant ium totre</p><span class="more">READ MORE</span></article>
<article class="abs card" style="left:834px"><h3 class="script">Live Music</h3><p>Sed ut perspiciatis unde isna tus error sit voluptatem accntm dioremque laudant ium totre</p><span class="more">READ MORE</span></article>
<div class="abs card-photo" style="left:191px;background:radial-gradient(circle,#b8893a,#6a7a2a 70%,#3a2a1a)" role="img" aria-label="Burger photo"></div>
<div class="abs card-photo" style="left:415px;background:radial-gradient(circle,#c4571e,#8a2e10 70%,#3a1a0a)" role="img" aria-label="Chicken wings photo"></div>
<div class="abs card-photo" style="left:638px;background:radial-gradient(circle,#e8a83a,#a8681a 65%,#2a1a10)" role="img" aria-label="Glass of beer photo"></div>
<div class="abs card-photo" style="left:863px;background:radial-gradient(circle,#e09030,#7a3810 60%,#1a0a05)" role="img" aria-label="Live music crowd photo"></div>

<h2 class="abs rest-title script">Our Restaurant</h2>
<p class="abs rest-text">Sed ut perspiciatis unde omnis iste natus error sit voluptatem accusantium do-loremque laudant ium, totam rem aperiam, eaque isa quae billo inventore veritatis et quasi architecto beatae vitae dicta sunt explicaboemo enim ipsamvoluptatem quia voluptas sit asperntur aut odit auSed ut pe rspiciatis unde omnis iste natus error sit voluptatem accusantiumquasi architecto beatae vitae dicta sunt explicaboemo enim ipsamvoluptatem quia voluptas sit asperntur aut odit .</p>

<div class="abs quick" style="left:162px"><div class="ring"><svg width="30" height="26" viewBox="0 0 30 26"><path d="M4 18a11 11 0 0 1 22 0Z" fill="#fff"/><rect x="1" y="19" width="28" height="3" fill="#fff"/><circle cx="15" cy="5" r="2" fill="#fff"/></svg></div><span>Menu</span></div>
<div class="abs quick" style="left:251px"><div class="ring"><svg width="26" height="26" viewBox="0 0 26 26"><rect x="2" y="4" width="22" height="20" fill="none" stroke="#fff" stroke-width="2"/><rect x="2" y="4" width="22" height="5" fill="#fff"/><path d="M7 13h3M12 13h3M17 13h3M7 18h3M12 18h3M17 18h3" stroke="#fff" stroke-width="2"/></svg></div><span>Reservation</span></div>
<div class="abs quick" style="left:340px"><div class="ring"><svg width="30" height="26" viewBox="0 0 30 26"><path d="M3 24 7 14h16l4 10Z" fill="none" stroke="#fff" stroke-width="2"/><path d="M15 18s-5-5-5-9a5 5 0 0 1 10 0c0 4-5 9-5 9Z" fill="#fff"/></svg></div><span>Location</span></div>

<div class="abs news-band"></div>
<div class="abs table-setting" role="img" aria-label="White dinner plate with knife and spoon on a white tablecloth"></div>
<div class="abs sign-photo" role="img" aria-label="Photo of the restaurant's red wooden sign on the shed"></div>
<h2 class="abs news-title script">Latest Restaurant News</h2>
<p class="abs news-text">Sed ut perspiciatis unde omnis iste natus error sit voluptatem accusantium doloremque laudant ium, totam rem aperiam, eaque isa quae billo inventore veritatis et quasi architecto beatae vitae dicta sunt explicaboemo enim ipsamvoluptatem quia voluptas sit asperntur aut odit auSed ut pe rspiciatis unde omnis iste natus error sit voluptatem accusantiumquasi architecto beatae vitae dicta sunt explicaboemo enim ipsamvoluptatem quia voluptas sit asperntur aut odit .</p>
<p class="abs news-meta">
  <svg width="10" height="10" viewBox="0 0 10 10"><rect x="0.5" y="1.5" width="9" height="8" fill="none" stroke="#333"/><rect x="0.5" y="1.5" width="9" height="2" fill="#333"/></svg> March 05 2015
  &nbsp;<svg width="11" height="10" viewBox="0 0 11 10"><path d="M1 1h9v6H5L2 9V7H1Z" fill="#333"/></svg> Comments
</p>
<div class="abs burger" role="img" aria-label="Photo of a cheeseburger with sesame bun"></div>

<h2 class="abs h-section script events-title">News &amp; Events</h2>
<article class="abs event" style="left:162px"><div class="event-photo" style="background:linear-gradient(135deg,#6a2a1a,#b89a7a 55%,#e8e2da)" role="img" aria-label="Table setting with wine glasses and napkin"></div><h4>Sed uterspiciatis undeomni</h4><p>Sed ut perspiciatis unde omnis iste natus error sit vol uptatem accusantium doloremque laudant ium, totam rem aperiam, eaque isa quae billo in</p><span class="more">READ MORE</span></article>
<article class="abs event" style="left:462px"><div class="event-photo" style="background:linear-gradient(135deg,#3a2a22,#9a604a 55%,#c8a688)" role="img" aria-label="Couple dining at the restaurant"></div><h4>Sed uterspiciatis undeomni</h4><p>Sed ut perspiciatis unde omnis iste natus error sit vol uptatem accusantium doloremque laudant ium, totam rem aperiam, eaque isa quae billo in</p><span class="more">READ MORE</span></article>
<article class="abs event" style="left:761px"><div class="event-photo" style="background:linear-gradient(135deg,#8a6a4a,#ddd6cc 55%,#f2f0ec)" role="img" aria-label="Waiter serving plated dishes"></div><h4>Sed uterspiciatis undeomni</h4><p>Sed ut perspiciatis unde omnis iste natus error sit vol uptatem accusantium doloremque laudant ium, totam rem aperiam, eaque isa quae billo in</p><span class="more">READ MORE</span></article>

<footer class="abs footer"></footer>
<div class="abs footer-rule" style="top:2413px"></div>
<div class="abs footer-rule" style="top:2420px;border-top-style:solid;border-color:#6a4a38"></div>
<div class="abs footer-badge">
  <svg width="32" height="32" viewBox="0 0 32 32"><path d="M11 8v16M9 8v5a2 2 0 0 0 4 0V8M21 8c-2 0-3 3-3 6h3v10" fill="none" stroke="#fff" stroke-width="1.6"/></svg>
</div>
<div class="abs footer-brand">Fizz's Shed<br>and Grill</div>

<div class="abs f-col" style="left:353px;width:190px">
  <h5>About us</h5>
  <p>Sed ut perspiciatis unde omnis iste na tus error sit vol uptatem accusantium doloremque laudant ium, totam rem aperiam, eaque isa quae ab illos error sit vol upta .</p>
  <p style="margin-top:14px">Speriam, eaque isa quae m, eaque ib illos error sit vol upta .</p>
</div>

<div class="abs f-col hours" style="left:603px">
  <h5>Opening hours</h5>
  <div>Mon - Fri<i></i>10 Am - 8 Pm</div>
  <div>Saturday<i></i>10 Am - 9 Pm</div>
  <div>Wednesday<i></i>10 Am - 3 Pm</div>
  <div class="sub">Bar Opening Hours</div>
  <div>Mon - Fri<i></i>10 Pm - 4 Am</div>
  <div>Saturday<i></i>10 Pm - 3 Pm</div>
  <div>Wednesday<i></i>10 Am - 3Pm</div>
</div>

<div class="abs f-col" style="left:887px;width:200px">
  <h5>Contact us</h5>
  <ul class="contact">
    <li><svg width="9" height="11" viewBox="0 0 9 11"><path d="M4.5 11S0 6 0 4a4.5 4.5 0 0 1 9 0c0 2-4.5 7-4.5 7Z" fill="#fff"/></svg><span>Postal address: PO Box 210,<br>Elm Row dummy adres sire lor</span></li>
    <li><svg width="10" height="10" viewBox="0 0 10 10"><path d="M2 0 4 2.5 3 4a6 6 0 0 0 3 3l1.5-1L10 8 8 10C3 9 1 6 0 2Z" fill="#fff"/></svg>Phone: 555-014-2231</li>
    <li><svg width="10" height="10" viewBox="0 0 10 10"><rect x="2" y="0" width="6" height="3" fill="#fff"/><rect x="0" y="3" width="10" height="5" fill="#fff"/><rect x="2" y="7" width="6" height="3" fill="#fff"/></svg>Fax: 555-014-2232</li>
    <li><svg width="10" height="8" viewBox="0 0 10 8"><rect width="10" height="8" fill="#fff"/><path d="M0 0 5 4 10 0" fill="none" stroke="#2e150a"/></svg>info@fizzshed.example</li>
  </ul>
  <div class="social"><span></span><span></span><span></span><span></span></div>
</div>

<p class="abs copyright">© 2016 Fizz's Shed and Grill.All copyrights are reserved &nbsp;Term of Use</p>

</body>
</html>
```